WordPress Website Design for Multi-Brand Aviation Group (Unified Branding System)

Project Overview:
We are seeking a professional, modern WordPress website design for an aviation-focused umbrella company that owns and operates multiple subsidiary businesses. The goal is to create a cohesive visual system that clearly communicates that each company operates under the same parent organization, while still allowing each brand to maintain a slightly distinct identity.
This is not just a single website design—we are looking for a scalable design framework that can be applied across multiple aviation-related businesses.
Objectives:
- Establish a consistent, recognizable brand identity across all company websites
Clearly communicate the relationship between the parent company and its subsidiaries
-bCreate a clean, high-end corporate aviation aesthetic
- Ensure all designs are SEO-friendly and optimized for performance
- Allow flexibility for future expansion (additional subsidiaries)
- Target Audience:
- Corporate aviation clients
- Charter customers
- Students wishing to receive flight training
- Aircraft owners and operators
- Turbine aircraft training to meet insurance requirements
- Business professionals and high-net-worth individuals
- Aviation industry partners
Design Direction & Style:
We are looking for a premium, professional aviation feel—think clean, modern, and high-trust. The design should reflect the standards of corporate aviation: precision, safety, and sophistication.
Key style notes:
Minimalist but impactful layout
High-quality aviation photography (jets, interiors, operations, global travel)
Subtle motion/interaction (hover effects, transitions)
Clear typography hierarchy for readability and professionalism
Branding Requirements:
Incorporate the primary colors of the parent company logo across all designs
Website Structure (Core Pages):
Design a system that includes:
Home Page with the following links:
- About / Company Overview
- Aircraft Management
- Aircraft Acquisition
- Charter
- Pilot Services
- Trip Support
- Contact Page
Site should further include:
- Mobile-first responsive design
- Fast-loading, performance-optimized layouts
SEO & Technical Considerations:
- Design should support high-level SEO implementation:
- Clean layout structure that translates well to semantic HTML
- Proper heading hierarchy (H1, H2, H3)
- Space for keyword-rich content without clutter
- Optimized image placement (with alt text capability)
- Fast load times (lightweight design approach)
- Compatibility with WordPress SEO plugins (e.g., Yoast or Rank Math)
WordPress Requirements:
- Design should be easily built using WordPress (preferred builders: Elementor, Gutenberg, or similar)
- Reusable templates for scalability across multiple sites
- Easy for non-developers to update text and images
- Modular components (blocks/sections that can be reused across pages and sites)
- Navigation & UX:
- Simple, intuitive navigation
- Sticky header preferred
Style guide including:
- Colors
- Fonts
- Button styles
- Layout system
- Designs similar to high-end corporate aviation, private jet charter, or luxury service brands are preferred—clean, sharp, and premium without being overly flashy.
What We Want to Avoid:
- Overly busy layouts
- Generic templates with no brand identity
- Outdated or “stock” looking aviation designs
- Poor mobile responsiveness
Additional Notes:
We are building a long-term brand system, not just a one-off website. There is potential for ongoing work as we expand additional subsidiary sites.
We value designers who understand branding consistency across multiple business units and can create a scalable, professional system.
Include the attached main company logo "Vireton Aviation Group" and the "Member PJFO" logo on the main page.

```html
<!DOCTYPE html>
<html lang="en">
<head>
<meta charset="utf-8">
<title>Vireton Aviation Group</title>
<link rel="stylesheet" href="https://fonts.googleapis.com/css2?family=Michroma&family=Lato:wght@400;700;900&display=swap">
<style>
:root{
  --blue:#0b55c4;
  --blue-bright:#1a6ae0;
  --blue-deep:#0a3f9a;
  --navy:#0a1733;
  --ink:#111522;
  --text:#3c4252;
  --soft:#eef1f6;
  --white:#fff;
}
*{box-sizing:border-box;margin:0;padding:0}
html,body{width:1200px;height:4800px;overflow:hidden}
body{position:relative;font-family:'Lato',sans-serif;color:var(--text);background:var(--white)}
section,header,footer{position:absolute;left:0;width:1200px}
.display{font-family:'Michroma',sans-serif;color:var(--ink);letter-spacing:1px;text-transform:uppercase;font-weight:400;-webkit-text-stroke:.8px currentColor}
.display em{font-style:normal;color:var(--blue)}
.btn{position:absolute;display:flex;align-items:center;color:#fff;font:700 15px 'Lato',sans-serif;text-transform:uppercase;background:var(--blue);padding-left:38px;clip-path:polygon(0 0,100% 0,86% 100%,0 100%)}
/* hero */
.hero{top:0;height:700px;background:#3a4048}
.hero-photo{position:absolute;inset:0;background:
  radial-gradient(ellipse 520px 300px at 960px 240px,rgba(232,236,240,.55),rgba(232,236,240,0) 70%),
  radial-gradient(ellipse 380px 140px at 600px 520px,rgba(20,22,26,.7),rgba(20,22,26,0) 75%),
  radial-gradient(ellipse 420px 120px at 1020px 500px,rgba(150,110,90,.35),rgba(150,110,90,0) 75%),
  linear-gradient(180deg,#4c535c 0%,#5b636d 40%,#6a6f73 62%,#3b3f44 100%)}
.hero-photo:after{content:"";position:absolute;inset:0;background:linear-gradient(90deg,rgba(24,28,36,.75) 0%,rgba(24,28,36,.35) 50%,rgba(24,28,36,.1) 100%)}
.brand{position:absolute;color:#fff;font:900 26px 'Lato',sans-serif;letter-spacing:2px;line-height:1}
.brand small{display:block;font:700 9px 'Lato',sans-serif;letter-spacing:3px;margin-top:3px}
.topbar{position:absolute;right:0;top:0;width:492px;height:48px;background:var(--blue);clip-path:polygon(4% 0,100% 0,100% 100%,0 100%);display:flex;align-items:center;gap:64px;padding-left:36px;color:#fff;font:700 14px/1.1 'Lato',sans-serif}
.topbar .item{display:flex;align-items:center;gap:12px}
.nav{position:absolute;top:74px;left:110px;display:flex;gap:22px;font:400 14px 'Lato',sans-serif;color:#e5e9f0;text-transform:uppercase}
.nav .on{color:#fff;font-weight:700;position:relative}
.nav .on:after{content:"";position:absolute;left:12px;right:12px;bottom:-10px;height:3px;background:var(--blue-bright)}
.follow{position:absolute;left:40px;top:228px;display:flex;flex-direction:column;align-items:center;gap:10px;color:#fff}
.follow span{writing-mode:vertical-rl;font:700 13px 'Lato',sans-serif;letter-spacing:1px;margin-bottom:6px}
.soc{width:26px;height:26px;border:2px solid #fff;border-radius:50%}
.hero-welcome{position:absolute;left:108px;top:186px;color:#fff;font:400 16px 'Michroma',sans-serif;letter-spacing:1px;-webkit-text-stroke:.4px #fff}
.hero-title{position:absolute;left:106px;top:212px;color:#fff;font-size:54px;line-height:64px}
.hero-copy{position:absolute;left:108px;top:358px;color:#fff;font-size:14px;line-height:24px;width:430px}
.slider-dots{position:absolute;right:104px;top:278px;display:flex;flex-direction:column;gap:20px}
.slider-dots i{width:6px;height:6px;border-radius:50%;background:var(--blue-bright)}
.slider-dots i:first-child{width:10px;height:10px;background:#fff;border:2px solid var(--blue-bright);margin-left:-2px}
/* expertise */
.expertise{top:690px;height:700px}
.expertise h2{position:absolute;top:16px;width:100%;text-align:center;font-size:38px}
.card{position:absolute;top:92px;width:225px;height:425px;background:var(--soft);box-shadow:0 2px 6px rgba(0,0,0,.12)}
.card .photo{position:absolute;left:10px;top:12px;width:205px;height:180px;border-bottom:5px solid var(--blue)}
.ph-cockpit{background:
  radial-gradient(circle at 30% 40%,rgba(230,150,70,.55),rgba(230,150,70,0) 30%),
  radial-gradient(circle at 75% 55%,rgba(210,120,60,.45),rgba(210,120,60,0) 28%),
  radial-gradient(ellipse at 50% 15%,rgba(120,130,150,.6),rgba(120,130,150,0) 55%),
  linear-gradient(180deg,#2c2f37,#16181e 60%,#2a2420)}
.ph-deck{background:
  radial-gradient(ellipse at 50% 25%,rgba(170,190,215,.75),rgba(170,190,215,0) 55%),
  radial-gradient(circle at 30% 70%,rgba(200,150,90,.35),rgba(200,150,90,0) 30%),
  linear-gradient(180deg,#3b4658,#15181f 55%,#0d0f14)}
.ph-charter{background:
  radial-gradient(circle at 40% 55%,rgba(210,170,80,.6),rgba(210,170,80,0) 22%),
  radial-gradient(ellipse at 75% 40%,rgba(245,247,250,.9),rgba(245,247,250,0) 45%),
  linear-gradient(180deg,#c7d6e6 0%,#dfe6ee 45%,#8d95a0 80%,#6b717a)}
.ph-crew{background:
  radial-gradient(ellipse at 50% 25%,rgba(235,240,248,.9),rgba(235,240,248,0) 50%),
  radial-gradient(ellipse at 60% 75%,rgba(20,30,60,.8),rgba(20,30,60,0) 55%),
  radial-gradient(circle at 85% 35%,rgba(190,60,50,.45),rgba(190,60,50,0) 25%),
  linear-gradient(180deg,#6f9ad4,#a8bcd6 40%,#4a5a78 75%,#7d8796)}
.card h3{position:absolute;left:17px;top:208px;color:var(--blue);font:400 21px/28px 'Lato',sans-serif;text-transform:uppercase}
.card p{position:absolute;left:17px;top:270px;width:175px;font-size:13.5px;line-height:21.5px;color:#333}
.card h3.one+p{top:240px}
.card .btn{left:0;bottom:0;width:180px;height:46px;font-size:15px}
/* trip */
.trip{top:1393px;height:540px}
.trip-bg{position:absolute;right:0;top:0;width:800px;height:540px;background:#f1f2f4}
.trip-photo{position:absolute;left:0;top:32px;width:607px;height:498px;clip-path:polygon(0 0,100% 0,74% 100%,0 100%);background:
  radial-gradient(ellipse at 18% 45%,rgba(25,28,36,.9),rgba(25,28,36,0) 35%),
  radial-gradient(circle at 56% 30%,rgba(215,170,140,.7),rgba(215,170,140,0) 18%),
  radial-gradient(circle at 60% 55%,rgba(200,40,40,.5),rgba(200,40,40,0) 14%),
  radial-gradient(ellipse at 40% 60%,rgba(40,44,55,.75),rgba(40,44,55,0) 35%),
  linear-gradient(110deg,#d8dadd,#a9b0bb 40%,#6c7686 75%,#4a5262)}
.trip h2{position:absolute;left:609px;top:154px;font-size:38px}
.trip p{position:absolute;left:612px;top:218px;width:460px;font-size:14px;line-height:23.5px;color:#333}
/* accreditations */
.accred{top:1952px;height:600px;background:radial-gradient(circle at 50% 45%,#1f73e3,#0b52c0 60%,#0a46a8)}
.accred .map{position:absolute;inset:0;background:
  radial-gradient(ellipse 260px 160px at 270px 250px,rgba(255,255,255,.07),rgba(255,255,255,0) 70%),
  radial-gradient(ellipse 300px 200px at 880px 230px,rgba(255,255,255,.07),rgba(255,255,255,0) 70%),
  radial-gradient(ellipse 160px 150px at 360px 470px,rgba(255,255,255,.06),rgba(255,255,255,0) 70%),
  radial-gradient(ellipse 180px 120px at 1020px 460px,rgba(255,255,255,.06),rgba(255,255,255,0) 70%)}
.accred h2{position:absolute;top:146px;width:100%;text-align:center;color:#fff;font-size:38px}
.member{position:absolute;top:200px;left:0;width:100%;display:flex;justify-content:center;align-items:center;gap:16px;color:#fff;font:400 38px 'Michroma',sans-serif;-webkit-text-stroke:.8px #fff}
.member .badge{width:44px;height:44px;border-radius:50%;border:3px solid #fff}
.stat{position:absolute;top:346px;width:220px;text-align:center;color:#fff}
.stat b{display:block;font:900 38px 'Lato',sans-serif}
.stat span{display:block;margin-top:10px;font:700 21px/29px 'Lato',sans-serif;text-transform:uppercase}
.divider{position:absolute;top:352px;height:110px;border-left:2px dashed rgba(255,255,255,.55)}
.node{position:absolute;width:12px;height:12px;border-radius:50%;background:#fff;box-shadow:0 0 10px 4px rgba(255,255,255,.35)}
/* about */
.about{top:2552px;height:652px;background:#eef2f9}
.about .eyebrow{position:absolute;left:108px;top:100px;font-size:16px;-webkit-text-stroke:.3px currentColor}
.about h2{position:absolute;left:106px;top:128px;font-size:40px;line-height:47px}
.about p{position:absolute;left:108px;width:478px;font-size:14px;line-height:23px;color:#333}
.about .frame{position:absolute;left:745px;top:62px;width:345px;height:395px;border:5px solid #d9dfe9}
.about .photo-main{position:absolute;left:680px;top:93px;width:382px;height:414px;background:
  radial-gradient(ellipse at 50% 30%,rgba(250,251,252,.95),rgba(250,251,252,0) 45%),
  radial-gradient(ellipse at 55% 72%,rgba(25,30,45,.55),rgba(25,30,45,0) 30%),
  linear-gradient(180deg,#6f9ee0 0%,#b9d0ee 25%,#e8ecf1 55%,#9aa3ad 80%,#7c858f)}
.about .photo-cabin{position:absolute;left:624px;top:378px;width:209px;height:181px;border:5px solid #fff;background:
  radial-gradient(ellipse at 50% 20%,rgba(230,235,242,.85),rgba(230,235,242,0) 50%),
  linear-gradient(180deg,#b7c1cd,#4e6290 45%,#203266 75%,#141f40)}
.years{position:absolute;left:615px;top:133px;width:140px;height:141px;background:var(--blue);padding:8px}
.years div{background:#fff;width:100%;height:100%;text-align:center;padding-top:18px;color:var(--ink)}
.years b{display:block;font:400 38px 'Michroma',sans-serif;-webkit-text-stroke:.8px currentColor}
.years span{display:block;font:700 15px/18px 'Lato',sans-serif;margin-top:6px}
/* partners */
.partners{top:3204px;height:382px}
.partners h2{position:absolute;top:98px;width:100%;text-align:center;font-size:38px}
.partner{position:absolute;top:206px;display:flex;align-items:center;gap:10px;transform:translateX(-50%);font:700 18px 'Lato',sans-serif;color:#2a3d6b}
.partner i{width:36px;height:36px;border-radius:50%;background:#c9d3e4}
/* quote */
.quote{top:3586px;height:652px;background:linear-gradient(180deg,#1660cc,#0d4fb4 50%,#0a3f92)}
.quote .apron{position:absolute;inset:0;background:
  radial-gradient(ellipse 300px 120px at 200px 420px,rgba(255,255,255,.08),rgba(255,255,255,0) 70%),
  radial-gradient(ellipse 340px 140px at 960px 380px,rgba(255,255,255,.08),rgba(255,255,255,0) 70%),
  radial-gradient(ellipse 500px 120px at 600px 600px,rgba(5,25,70,.35),rgba(5,25,70,0) 70%)}
.quote .notch{position:absolute;top:0;left:0}
.carousel{position:absolute;top:8px;left:568px;display:flex;gap:18px;align-items:center}
.carousel i{width:6px;height:6px;border-radius:50%;background:#8793a8}
.carousel i:first-child{width:14px;height:14px;border:3px solid var(--blue);background:#fff}
.quote .eyebrow{position:absolute;top:154px;width:100%;text-align:center;color:#fff;font-size:16px;-webkit-text-stroke:.3px #fff}
.quote h2{position:absolute;top:186px;width:100%;text-align:center;color:#fff;font-size:40px}
.field{position:absolute;background:#fff;display:flex;align-items:flex-start;padding:20px 14px;gap:12px;font:400 14px 'Lato',sans-serif;color:#666;text-transform:uppercase}
.submit{position:absolute;left:490px;top:556px;width:160px;height:46px;background:#fff;color:var(--ink);font:900 15px 'Lato',sans-serif;display:flex;align-items:center;justify-content:center;clip-path:polygon(0 0,100% 0,86% 100%,0 100%)}
/* footer */
.footer{top:4238px;height:562px;background:radial-gradient(circle at 80% 20%,#0e2a6a,#0a1a3f 60%,#081330)}
.footer .brand{left:108px;top:140px}
.footer .about-text{position:absolute;left:108px;top:194px;width:262px;color:#c7cedd;font-size:12.5px;line-height:21px}
.footer .socials{position:absolute;left:108px;top:330px;display:flex;gap:8px}
.footer .socials .soc{width:27px;height:27px}
.col{position:absolute;top:136px;color:#fff}
.col h4{font:900 18px 'Lato',sans-serif;text-transform:uppercase;margin-bottom:22px}
.col li{list-style:none;font-size:14px;color:#b9c2d4;height:36px}
.contact-row{display:flex;gap:16px;margin-bottom:22px;font-size:12.5px;line-height:21px;color:#b9c2d4;width:300px}
.contact-row i{flex:none;width:26px;height:26px;border-radius:50%;background:var(--blue);display:flex;align-items:center;justify-content:center}
.copyright{position:absolute;bottom:0;left:0;width:100%;height:30px;background:#050b1c;color:#fff;font-size:12px;text-align:center;line-height:30px}
.copyright em{font-style:normal;color:var(--blue-bright)}
</style>
</head>
<body>

<header class="hero">
  <div class="hero-photo" role="img" aria-label="Commercial jet airliner parked on the apron at dusk"></div>
  <div class="brand" style="left:108px;top:18px">VIRETON<small>AVIATION GROUP</small></div>
  <div class="topbar">
    <div class="item">
      <svg width="20" height="20" viewBox="0 0 20 20"><circle cx="10" cy="10" r="10" fill="#fff" opacity=".2"/><rect x="5" y="6.5" width="10" height="7" fill="none" stroke="#fff" stroke-width="1.4"/><path d="M5 6.5l5 4 5-4" fill="none" stroke="#fff" stroke-width="1.4"/></svg>
      <div>MAIL :<br>vireton@mail.com</div>
    </div>
    <div class="item">
      <svg width="20" height="20" viewBox="0 0 20 20"><circle cx="10" cy="10" r="10" fill="#fff" opacity=".2"/><path d="M7 5l2 3-1 1.5c.8 1.5 1.7 2.4 3 3L12.5 11l3 2-1 2c-4 0-8.5-4.5-8.5-8.5z" fill="#fff"/></svg>
      <div>CALL US :<br>555-010-2040</div>
    </div>
  </div>
  <nav class="nav">
    <span class="on">Home</span><span>About</span><span>Aircraft Management</span><span>Aircraft Acquisition</span><span>Charter</span><span>Pilot Services</span><span>Trip Support</span><span>Contact</span>
  </nav>
  <div class="follow"><span>FOLLOW US :</span><i class="soc" aria-label="Social profile"></i><i class="soc" aria-label="Social profile"></i><i class="soc" aria-label="Social profile"></i><i class="soc" aria-label="Social profile"></i></div>
  <div class="hero-welcome">WELCOME TO</div>
  <h1 class="display hero-title">Vireton<br>Aviation</h1>
  <p class="hero-copy">Many desktop publishing packages and web page editors now use Lorem Ipsum as their default model text</p>
  <a class="btn" style="left:108px;top:428px;width:180px;height:45px;padding-left:28px">View Services</a>
  <div class="slider-dots"><i></i><i></i><i></i><i></i></div>
  <svg width="1200" height="700" viewBox="0 0 1200 700" style="position:absolute;left:0;top:0">
    <path d="M0 665L600 598L1200 665L1200 700L0 700Z" fill="var(--blue)"/>
    <path d="M0 694L600 622L1200 694L1200 700L0 700Z" fill="#fff"/>
    <circle cx="600" cy="605" r="44" fill="#fff"/>
    <circle cx="600" cy="605" r="36" fill="var(--blue)"/>
  </svg>
</header>

<section class="expertise">
  <h2 class="display">Areas of <em>Expertise</em></h2>
  <article class="card" style="left:106px"><div class="photo ph-cockpit" role="img" aria-label="Cockpit instrument panel"></div><h3>Aircraft<br>Management</h3><p>Many desktop publishing packages and web page editors now use...</p><a class="btn">Learn More</a></article>
  <article class="card" style="left:358px"><div class="photo ph-deck" role="img" aria-label="Pilots at the controls in a flight deck"></div><h3>Aircraft<br>Acquisition</h3><p>Many desktop publishing packages and web page editors now use...</p><a class="btn">Learn More</a></article>
  <article class="card" style="left:615px"><div class="photo ph-charter" role="img" aria-label="Passengers boarding a private jet"></div><h3 class="one">Charter</h3><p>Many desktop publishing packages and web page editors now use Many desktop publishing packages and ...</p><a class="btn">Learn More</a></article>
  <article class="card" style="left:868px"><div class="photo ph-crew" role="img" aria-label="Flight crew walking on the tarmac"></div><h3>Pilot<br>Services</h3><p>Many desktop publishing packages and web page editors now use...</p><a class="btn">Learn More</a></article>
</section>

<section class="trip">
  <div class="trip-bg"></div>
  <div class="trip-photo" role="img" aria-label="Traveller handing documents to an agent at a check-in desk"></div>
  <h2 class="display">Trip <em>Support</em></h2>
  <p>Lorem Ipsum has been the industry's standard dummy text ever since the 1500s, when an unknown printer took a galley of type and scrambled it to make a type specimen book. It has survived not only five centuries, but also the leap into electronic typesetting, remaining essentially unchanged.</p>
  <a class="btn" style="left:612px;top:353px;width:170px;height:45px">Read More</a>
</section>

<section class="accred">
  <div class="map" role="img" aria-label="Faint world map with flight routes"></div>
  <h2 class="display">Accreditations</h2>
  <div class="member"><span>MEMBER OF</span><i class="badge"></i><span>PJFO</span></div>
  <i class="node" style="left:377px;top:66px"></i><i class="node" style="left:467px;top:77px"></i>
  <i class="node" style="left:194px;top:288px"></i><i class="node" style="left:940px;top:246px"></i>
  <i class="node" style="left:614px;top:336px"></i><i class="node" style="left:352px;top:516px"></i>
  <i class="node" style="left:646px;top:530px"></i><i class="node" style="left:1058px;top:548px"></i>
  <div class="stat" style="left:108px"><b>50+</b><span>Aircraft<br>Handled</span></div>
  <div class="divider" style="left:343px"></div>
  <div class="stat" style="left:361px"><b>1628+</b><span>Sectors<br>Operated</span></div>
  <div class="divider" style="left:600px"></div>
  <div class="stat" style="left:618px"><b>2460+</b><span>Charter<br>Customers</span></div>
  <div class="divider" style="left:855px"></div>
  <div class="stat" style="left:872px"><b>355+</b><span>Private<br>Aircraft</span></div>
</section>

<section class="about">
  <div class="display eyebrow">About Us</div>
  <h2 class="display">Key Facts<br>of Aviation<br><em>Expertise</em></h2>
  <p style="top:290px">Lorem Ipsum has been the industry's standard dummy text ever since the 1500s, when an unknown printer took a galley of type and scrambled it to make a type specimen book. It has survived not only five centuries, but also the leap into electronic typesetting, remaining essentially unchanged.</p>
  <p style="top:412px">It was popularised in the 1960s with the release of Typesheet sheets containing Lorem Ipsum passages, and more recently with desktop publishing software like Verso Layout</p>
  <a class="btn" style="left:108px;top:505px;width:180px;height:45px">Read More</a>
  <div class="frame"></div>
  <div class="photo-main" role="img" aria-label="Pilot standing in front of a jet airliner"></div>
  <div class="photo-cabin" role="img" aria-label="Aircraft cabin seating"></div>
  <div class="years"><div><b>25</b><span>YEARS<br>EXPERIENCE</span></div></div>
</section>

<section class="partners">
  <h2 class="display">Global <em>Partners</em></h2>
  <div class="partner" style="left:192px"><i></i>Crewlink</div>
  <div class="partner" style="left:434px"><i></i>Northwind</div>
  <div class="partner" style="left:714px"><i></i>Skyfair</div>
  <div class="partner" style="left:982px"><i></i>Aloft</div>
</section>

<section class="quote">
  <div class="apron" role="img" aria-label="Airport apron seen from above in blue tones"></div>
  <svg class="notch" width="1200" height="110" viewBox="0 0 1200 110">
    <path d="M0 0H1200V30L600 108L0 30Z" fill="#0b1328"/>
    <path d="M0 0H1200L600 98Z" fill="#fff"/>
  </svg>
  <div class="carousel"><i></i><i></i><i></i></div>
  <div class="display eyebrow">Contact Us</div>
  <h2 class="display">Get a Quote</h2>
  <div class="field" style="left:192px;top:259px;width:400px;height:60px">
    <svg width="12" height="14" viewBox="0 0 12 14"><circle cx="6" cy="4" r="3" fill="var(--blue)"/><path d="M0 14c0-4 2.5-6 6-6s6 2 6 6z" fill="var(--blue)"/></svg>First Name</div>
  <div class="field" style="left:605px;top:259px;width:403px;height:60px">
    <svg width="12" height="14" viewBox="0 0 12 14"><circle cx="6" cy="4" r="3" fill="var(--blue)"/><path d="M0 14c0-4 2.5-6 6-6s6 2 6 6z" fill="var(--blue)"/></svg>Last Name</div>
  <div class="field" style="left:192px;top:332px;width:400px;height:59px">
    <svg width="14" height="12" viewBox="0 0 14 12"><rect width="14" height="11" fill="var(--blue)"/><path d="M0 1l7 5 7-5" fill="none" stroke="#fff" stroke-width="1.3"/></svg>Email</div>
  <div class="field" style="left:605px;top:332px;width:403px;height:59px">
    <svg width="13" height="13" viewBox="0 0 13 13"><path d="M2 0l3 3.5-1.5 2c1 2 2 3 4 4L9.5 8l3.5 3-1.5 2C6 13 0 7 0 1.5z" fill="var(--blue)"/></svg>Phone No</div>
  <div class="field" style="left:192px;top:401px;width:816px;height:140px">
    <svg width="13" height="12" viewBox="0 0 13 12"><path d="M0 0h13v8H5l-3 3V8H0z" fill="var(--blue)"/></svg>Message</div>
  <div class="submit">SUBMIT NOW</div>
</section>

<footer class="footer">
  <div class="brand">VIRETON<small>AVIATION GROUP</small></div>
  <p class="about-text">Lorem Ipsum has been the industry's standard dummy text ever since the 1500s, when an unknown printer took a galley of type and scrambled it to make a type specimen book.</p>
  <div class="socials"><i class="soc" aria-label="Social profile"></i><i class="soc" aria-label="Social profile"></i><i class="soc" aria-label="Social profile"></i><i class="soc" aria-label="Social profile"></i></div>
  <div class="col" style="left:415px"><h4>Quick Link</h4><ul><li>Home</li><li>About</li><li>Aircraft Management</li><li>Aircraft Acquisition</li><li>Charter</li><li>Pilot Services</li><li>Trip Support</li><li>Contact</li></ul></div>
  <div class="col" style="left:635px"><h4>Quick Contact</h4>
    <div class="contact-row"><i><svg width="10" height="13" viewBox="0 0 10 13"><path d="M5 0a5 5 0 0 1 5 5c0 3.5-5 8-5 8S0 8.5 0 5a5 5 0 0 1 5-5z" fill="#fff"/><circle cx="5" cy="5" r="1.8" fill="var(--blue)"/></svg></i><span>1180 W Harbor Ave STE 210 Larkfield,<br>AZ 85099</span></div>
    <div class="contact-row"><i><svg width="12" height="10" viewBox="0 0 12 10"><rect width="12" height="9" fill="#fff"/><path d="M0 1l6 4 6-4" fill="none" stroke="var(--blue)" stroke-width="1.2"/></svg></i><span>info@vireton-aviation.example</span></div>
    <div class="contact-row"><i><svg width="12" height="12" viewBox="0 0 13 13"><path d="M2 0l3 3.5-1.5 2c1 2 2 3 4 4L9.5 8l3.5 3-1.5 2C6 13 0 7 0 1.5z" fill="#fff"/></svg></i><span>1-800-555-0142 (US/CAN)<br>International: +1-555-014-2200</span></div>
  </div>
  <div class="col" style="left:954px"><h4>Support</h4><ul><li>Help</li><li>Privacy policy</li><li>Terms &amp; Conditions</li><li>Career</li></ul></div>
  <div class="copyright">© 2026 <em>VIRETON AVIATION GROUP</em>. All rights reserved.</div>
</footer>

</body>
</html>
```